Moravel Aesthetic Doctor

I require an elegant, luxurious looking business card for my aesthetic business. I am a doctor and that will set me aside from competitors. I am planning to provide home and spa based treatments to clients with high expectations. I have attached my logo.

```html
<!DOCTYPE html>
<html lang="en">
<head>
<meta charset="utf-8">
<title>Moravel Aesthetic Doctor – Business Card</title>
<link rel="stylesheet" href="https://fonts.googleapis.com/css2?family=Libre+Baskerville:wght@400;700&family=Quicksand:wght@400;500&display=swap">
<style>
  :root {
    --bg: #d9dadc;
    --paper: #ffffff;
    --ink-black: #0b0b0c;
    --brand-blue: #1ba1e2;
    --grey-text: #8d8f93;
    --grey-line: #a9abae;
    --logo-grey: #8a8c90;
  }
  * { box-sizing: border-box; margin: 0; padding: 0; }
  html, body { width: 1200px; height: 965px; overflow: hidden; }
  body {
    background: var(--bg);
    font-family: "Quicksand", sans-serif;
    position: relative;
  }
  .card {
    position: absolute;
    left: 250px;
    width: 700px;
    height: 400px;
    background: var(--paper);
    box-shadow: 0 6px 18px rgba(0,0,0,.18);
    overflow: hidden;
  }
  .card--front { top: 55px; }
  .card--back { top: 510px; }

  /* Brand name block: one font, one weight, one colour */
  .brand {
    display: flex; align-items: center; gap: 22px;
  }
  .brand-ring {
    flex: none;
    width: 110px; height: 110px;
    border: 3px solid var(--logo-grey);
    border-radius: 50%;
  }
  .brand-name {
    font-family: "Libre Baskerville", serif;
    font-weight: 400;
    font-size: 36px;
    line-height: 1.25;
    color: var(--logo-grey);
    white-space: nowrap;
  }

  /* Front */
  .front-brand { position: absolute; left: 150px; top: 80px; }
  .front-rule {
    position: absolute;
    left: 500px; right: 40px; top: 222px;
    height: 1px; background: var(--grey-line);
  }
  .front-tagline {
    position: absolute;
    left: 40px; right: 40px; top: 305px;
    display: flex; align-items: center; gap: 18px;
  }
  .front-tagline .rule { flex: 1; height: 1px; background: var(--grey-line); }
  .front-tagline .text {
    font-family: "Libre Baskerville", serif;
    font-size: 15px; letter-spacing: 1px;
    color: var(--brand-blue);
  }

  /* Back */
  .back-strip {
    position: absolute; left: 0; top: 0; bottom: 0;
    width: 190px; background: var(--ink-black);
  }
  .strip-brand {
    position: absolute;
    left: 50%; top: 50%;
    width: 370px; height: 150px;
    transform: translate(-50%, -50%) rotate(-90deg);
    gap: 16px;
  }
  .strip-brand .brand-ring { width: 84px; height: 84px; }
  .strip-brand .brand-name { font-size: 28px; }

  .back-body { position: absolute; left: 230px; right: 20px; top: 40px; bottom: 30px; }
  .doctor-name { display: flex; align-items: baseline; gap: 10px; }
  .doctor-name .name {
    font-family: "Libre Baskerville", serif;
    font-weight: 700; font-size: 28px; color: var(--brand-blue);
  }
  .doctor-name .divider { width: 2px; height: 26px; background: var(--ink-black); align-self: center; }
  .doctor-name .post { font-size: 16px; color: var(--grey-text); letter-spacing: 1px; }
  .credential { font-size: 17px; color: var(--grey-text); margin-top: 4px; }

  .contact-list { list-style: none; margin-top: 50px; }
  .contact-list li {
    display: flex; align-items: center; gap: 12px;
    font-size: 18px; color: var(--grey-text); line-height: 1.5;
  }
  .contact-list svg { width: 18px; height: 18px; flex: none; }
  .contact-list .web strong { color: var(--brand-blue); font-weight: 500; }

  .services {
    position: absolute; left: 0; bottom: 10px;
    font-size: 16.5px; line-height: 1.35; color: var(--brand-blue);
    white-space: nowrap;
  }
</style>
</head>
<body>

<section class="card card--front" aria-label="Card front">
  <div class="brand front-brand">
    <div class="brand-ring" aria-hidden="true"></div>
    <p class="brand-name">Moravel<br>Aesthetic Doctor</p>
  </div>
  <div class="front-rule"></div>
  <div class="front-tagline">
    <span class="rule"></span>
    <span class="text">HOME AND SPA BASED TREATMENTS</span>
    <span class="rule"></span>
  </div>
</section>

<section class="card card--back" aria-label="Card back">
  <div class="back-strip">
    <div class="brand strip-brand">
      <div class="brand-ring" aria-hidden="true"></div>
      <p class="brand-name">Moravel<br>Aesthetic Doctor</p>
    </div>
  </div>

  <div class="back-body">
    <div class="doctor-name">
      <span class="name">Dr Elise Varner</span>
      <span class="divider"></span>
      <span class="post">MRCPCH MD</span>
    </div>
    <p class="credential">Australasian Diploma of Aesthetic Medicine</p>

    <ul class="contact-list">
      <li>
        <svg viewBox="0 0 24 24" fill="none" stroke="#1ba1e2" stroke-width="2" stroke-linecap="round" stroke-linejoin="round"><path d="M5 3h4l2 5-2.5 1.5a11 11 0 0 0 6 6L16 13l5 2v4a2 2 0 0 1-2 2A16 16 0 0 1 3 5a2 2 0 0 1 2-2z"/></svg>
        0800 555 018
      </li>
      <li>
        <svg viewBox="0 0 24 24" fill="none" stroke="#1ba1e2" stroke-width="2" stroke-linejoin="round"><rect x="3" y="5" width="18" height="14" rx="2"/><path d="M3 7l9 6 9-6"/></svg>
        elise@moravel.co.nz
      </li>
      <li class="web">
        <svg viewBox="0 0 24 24" fill="none" stroke="#1ba1e2" stroke-width="2"><circle cx="12" cy="12" r="9"/><path d="M3 12h18M12 3c3 3 3 15 0 18M12 3c-3 3-3 15 0 18"/></svg>
        <span>www.<strong>moravel</strong>.co.nz</span>
      </li>
    </ul>

    <p class="services">
      Dermal injectables - Plasma facials - Microneedling<br>
      Skin boosters - Excessive sweating<br>
      Home and Spa Based Treatments
    </p>
  </div>
</section>

</body>
</html>
```